Stationery Design Project for Marketing Consultancy

I have started a new consultancy business and require the following elements to be designed using existing logo:
• Business card
• Letterhead
• Envelope (DL, C4, C5)
• Microsoft word template for report writing
• A4 Presentation Folder
• Powerpoint template
COPY FOR FRONT AND BACK OF BUSINESS CARD
logo
'Measurable Marketing. Epic Results' slogan (but no need to use existing lockup with logo)
name, B Bus. Mktg, Grad Dip Digital Mktg, CPM (post nominal abbreviations in smaller font)
mobile: 04XX-XXX-XXX (I will give details to the winner to add)
website: www.tolvarin.com.au
email: info@tolvarin.com.au
COPY FOR LETTERHEAD
Logo
Company Name
Please, submit your designs that include business card, letterhead and envelope. Once selected the winner will be asked to complete the project by creating the rest of the artwork.
FINAL FILES
Print ready files to be supplied as well as Indesign files so that minor amends can be made if necessary in future.
• Layered vectors in EPS & PDF
• Screen quality JPEG & PNGs
ABOUT THE BUSINESS: TOLVARIN
I work with clients to understand their business challenges, developing and executing measurable marketing strategies tied to key business metrics. Services include:
Services include:
• Business planning and business development
• Marketing and brand strategy
• Insight-driven integrated campaigns
• Loyalty programs and retention marketing
• Marketing automation
• Direct marketing (traditional and digital)
• Content strategy and development
Hi everyone,
Target Market(s)
Corporate decision makers (heads of marketing, general managers etc) and small to medium sized business owners. Predominately male aged 35+
Industry/Entity Type
Marketing
Requirements
Must have
- BRAND PERSONALITY
The successful design will communicate brand personality. I am a professional, results-driven entrepreneur, but want to show off my creative flair.
MEMORABILITY
Looking for a unique and eye-catching design. Am considering special printing effects (die cuts, letterpress, interactive elements, embossing, foiling etc) or a striking minimalist approach.
Nice to have
- I have a mission that could be incorporated on reverse if room -
Turning insights into actions & passion into profit.
Should not have
- Use of pink or green.

```html
<!DOCTYPE html>
<html lang="en">
<head>
<meta charset="utf-8">
<title>Tolvarin Stationery</title>
<link href="https://fonts.googleapis.com/css2?family=Open+Sans:wght@400;600;700;800&display=swap" rel="stylesheet">
<style>
  :root {
    --backdrop: #e9e6e2;
    --ink-dark: #2b2b2b;
    --band-dark: #2f2f2f;
    --paper: #f4f4f4;
    --paper-edge: #e2e2e2;
    --mark-light: #d9d9d9;
    --text-dark: #262626;
    --text-muted: #8a8a8a;
    --ghost: #e6e6e6;
  }
  * { margin: 0; padding: 0; box-sizing: border-box; }
  html, body { width: 1200px; height: 818px; overflow: hidden; }
  body {
    background: var(--backdrop);
    font-family: "Open Sans", Arial, sans-serif;
    position: relative;
  }
  .piece { position: absolute; box-shadow: 0 2px 6px rgba(0,0,0,.25); }

  .brand { display: flex; flex-direction: column; align-items: center; }
  .brand-dot { border-radius: 50%; background: var(--mark-light); }
  .brand-name { font-weight: 800; color: var(--mark-light); letter-spacing: .04em; line-height: 1; }
  .brand-tagline { font-weight: 600; color: var(--text-muted); letter-spacing: .08em; text-transform: uppercase; line-height: 1; }

  /* Business cards */
  .card { width: 128px; height: 85px; top: 224px; background: var(--ink-dark); }
  .card-front { left: 287px; }
  .card-front .brand { position: absolute; left: 0; right: 0; top: 14px; }
  .card-front .brand-dot { width: 24px; height: 24px; margin-bottom: 5px; }
  .card-front .brand-name { font-size: 13px; }
  .card-front .brand-tagline { font-size: 3.6px; margin-top: 4px; }
  .card-back { left: 432px; }
  .card-back .brand { position: absolute; right: 8px; top: 6px; }
  .card-back .brand-dot { width: 10px; height: 10px; margin-bottom: 2px; }
  .card-back .brand-name { font-size: 5px; }
  .card-contact { position: absolute; left: 26px; top: 26px; color: #e0e0e0; font-size: 4px; line-height: 6px; }
  .card-contact .contact-name { font-size: 6px; font-weight: 700; margin-bottom: 7px; }

  /* Letterhead */
  .letterhead { left: 287px; top: 350px; width: 291px; height: 386px; background: var(--paper); }
  .letterhead-band { height: 37px; background: var(--band-dark); position: relative; }
  .letterhead-band .brand { position: absolute; left: 14px; top: 5px; }
  .letterhead-band .brand-dot { width: 14px; height: 14px; margin-bottom: 2px; }
  .letterhead-band .brand-name { font-size: 6.5px; }
  .letterhead-ghost { position: absolute; left: 60px; top: 110px; width: 170px; height: 170px; border-radius: 50%; background: var(--ghost); }

  .footer-line { position: absolute; font-size: 4.6px; color: var(--text-dark); white-space: nowrap; }
  .footer-line b { font-weight: 700; }
  .footer-line .sep { color: var(--text-muted); padding: 0 2px; }
  .letterhead .footer-line { left: 0; right: 0; bottom: 12px; text-align: center; }

  /* DL envelope */
  .envelope-dl { left: 624px; top: 86px; width: 317px; height: 151px; background: var(--paper); }
  .envelope-dl-band { height: 32px; background: var(--band-dark); position: relative; }
  .envelope-dl-band .brand { position: absolute; left: 14px; top: 3px; }
  .envelope-dl-band .brand-dot { width: 14px; height: 14px; margin-bottom: 2px; }
  .envelope-dl-band .brand-name { font-size: 6.5px; }
  .envelope-dl .footer-line { left: 0; right: 0; bottom: 8px; text-align: center; }

  /* C4 envelope */
  .envelope-c4 { left: 626px; top: 266px; width: 314px; height: 468px; background: var(--paper); }
  .envelope-c4 svg.flap { position: absolute; left: 0; top: 0; }
  .envelope-c4 .flap-brand { position: absolute; left: 0; right: 0; top: 10px; }
  .flap-brand .brand-dot { width: 32px; height: 32px; margin-bottom: 4px; }
  .flap-brand .brand-name { font-size: 14px; }
  .flap-brand .brand-tagline { font-size: 3.6px; margin-top: 3px; color: #9a9a9a; }
  .envelope-c4 .side-brand {
    position: absolute; left: 18px; bottom: 24px;
    display: flex; align-items: flex-end; gap: 8px;
  }
  .side-brand .brand-dot { width: 36px; height: 36px; background: var(--ink-dark); }
  .side-brand .vertical {
    writing-mode: vertical-rl; transform: rotate(180deg);
    display: flex; gap: 3px;
  }
  .side-brand .brand-name { color: #444; font-size: 15px; }
  .side-brand .brand-tagline { font-size: 3.8px; }
</style>
</head>
<body>

  <section class="piece card card-front">
    <div class="brand">
      <span class="brand-dot"></span>
      <span class="brand-name">TOLVARIN</span>
      <span class="brand-tagline">Measurable Marketing</span>
    </div>
  </section>

  <section class="piece card card-back">
    <div class="brand">
      <span class="brand-dot"></span>
      <span class="brand-name">TOLVARIN</span>
    </div>
    <div class="card-contact">
      <p class="contact-name">Company Name</p>
      <p>M: 0400 000 000</p>
      <p>info@tolvarin.com.au</p>
      <p>www.tolvarin.com.au</p>
    </div>
  </section>

  <section class="piece letterhead">
    <header class="letterhead-band">
      <div class="brand">
        <span class="brand-dot"></span>
        <span class="brand-name">TOLVARIN</span>
      </div>
    </header>
    <div class="letterhead-ghost" aria-hidden="true"></div>
    <p class="footer-line"><b>Company Name</b><span class="sep">|</span>M: 0400 000 000<span class="sep">|</span>E: info@tolvarin.com.au<span class="sep">|</span>www.tolvarin.com.au</p>
  </section>

  <section class="piece envelope-dl">
    <header class="envelope-dl-band">
      <div class="brand">
        <span class="brand-dot"></span>
        <span class="brand-name">TOLVARIN</span>
      </div>
    </header>
    <p class="footer-line"><b>Company Name</b><span class="sep">|</span>M: 0400 000 000<span class="sep">|</span>E: info@tolvarin.com.au<span class="sep">|</span>www.tolvarin.com.au</p>
  </section>

  <section class="piece envelope-c4">
    <svg class="flap" width="314" height="76" viewBox="0 0 314 76" aria-hidden="true">
      <path d="M0 0 H314 V55 Q298 58 292 76 H22 Q16 58 0 55 Z" fill="var(--band-dark)"/>
    </svg>
    <div class="brand flap-brand">
      <span class="brand-dot"></span>
      <span class="brand-name">TOLVARIN</span>
      <span class="brand-tagline">Measurable Marketing. Epic Results.</span>
    </div>
    <div class="side-brand">
      <span class="brand-dot"></span>
      <div class="vertical">
        <span class="brand-name">TOLVARIN</span>
        <span class="brand-tagline">Measurable Marketing. Epic Results.</span>
      </div>
    </div>
  </section>

</body>
</html>
```